Postcard design to acquire new clients for my Property Management Company

I'm looking for a postcard design that I can send to prospective clients detailing information about my company and services.
Postcard should be eye catching and contain information from www.bramblecrestpm.com. I've provided a few screen shots for the most important information and my logo.
Target Market(s)
Real Estate
Industry/Entity Type
Real Estate
Font styles to use
Sans Serif
Requirements
Must have
- Must be eye catching!! this will be a direct mail piece - I'd like for the card to be read and not tossed in the trash immediately.
Design que from the logo.
A place to write / print the receipts name and address.
our physical address - 2387 Hollow Pine Road, Lubbock, TX 79852.
Should not have
- the contact information on the business card is not accurate - please use info from website.

```html
<!DOCTYPE html>
<html lang="en">
<head>
<meta charset="utf-8">
<title>Bramblecrest Property Management Postcard</title>
<link rel="stylesheet" href="https://fonts.googleapis.com/css2?family=Montserrat:ital,wght@0,400;0,500;0,600;0,700;0,800;1,500&display=swap">
<style>
  :root{
    --navy:#1d4a8a;
    --navy-dark:#173d73;
    --grey:#5f6063;
    --grey-mid:#8b8c8e;
    --grey-light:#e6e6e7;
    --paper:#ffffff;
    --backdrop:#e9e8ea;
    --text:#3d3e40;
  }
  *{box-sizing:border-box;margin:0;padding:0}
  html,body{width:1200px;height:867px;overflow:hidden}
  body{background:var(--backdrop);font-family:"Montserrat",sans-serif;color:var(--text);position:relative}
  .postcard{position:absolute;top:250px;width:550px;height:367px;background:var(--paper);overflow:hidden;box-shadow:0 6px 18px rgba(0,0,0,.12)}
  .postcard--back{left:35px}
  .postcard--front{left:615px}

  /* Back side */
  .offer{position:absolute;left:0;top:0;width:275px;height:367px}
  .offer__title{position:absolute;left:26px;top:34px;line-height:1.02}
  .offer__lead{font-size:19px;font-weight:700;color:var(--grey);display:block}
  .offer__lead em{font-style:normal;color:var(--navy)}
  .offer__main{font-size:24px;font-weight:800;color:var(--grey);display:block}
  .offer__rule{position:absolute;left:26px;top:90px;width:230px;height:4px;background:var(--grey)}
  .offer__band{position:absolute;left:26px;top:100px;width:230px;height:20px;background:var(--grey);color:#fff;font-size:10px;font-weight:600;padding:4px 10px}
  .offer__box{position:absolute;left:26px;top:120px;width:230px;height:120px;background:var(--grey-light);padding:12px 14px;font-size:10px;line-height:1.35;color:var(--grey-mid)}
  .offer__box p+p{margin-top:10px}
  .offer__cta{position:absolute;left:26px;top:256px}
  .offer__cta-label{font-size:13px;font-weight:700;color:var(--grey)}
  .offer__phone{display:inline-block;margin-top:4px;background:var(--navy);color:#fff;font-size:22px;font-weight:800;border-radius:18px;padding:3px 20px}
  .offer__web{font-size:13px;font-weight:700;color:var(--grey);margin-top:5px}
  .offer__stripe{position:absolute;left:0;bottom:0;width:275px;height:12px;background:var(--navy)}
  .offer__stripe::before{content:"";position:absolute;left:140px;top:-8px;width:135px;height:8px;background:var(--grey)}
  .mailing{position:absolute;left:275px;top:0;width:275px;height:367px;border-left:1px solid var(--grey-light)}
  .mailing__line{position:absolute;left:30px;width:215px;height:1px;background:var(--grey-light)}

  /* Front side */
  .brand{position:absolute;left:28px;top:20px;line-height:1}
  .brand__name{font-size:20px;font-weight:700;color:var(--navy);letter-spacing:1px}
  .brand__tag{font-size:7.5px;font-weight:500;color:var(--navy);letter-spacing:1.4px;margin-top:3px}
  .photo{position:absolute;left:250px;top:55px;width:300px;height:145px;background:linear-gradient(120deg,#d9dde3 0%,#9aa6b6 45%,#3d4c66 75%,#cdd3db 100%)}
  .headline{position:absolute;left:28px;top:78px;line-height:1}
  .headline__small{font-size:14px;font-weight:500;color:var(--grey);display:block}
  .headline__big{font-size:29px;font-weight:800;color:var(--navy);display:block;letter-spacing:-.3px;line-height:.95}
  .services-band{position:absolute;left:0;top:200px;width:550px;height:4px;background:var(--navy)}
  .services-band__label{position:absolute;left:0;top:200px;width:200px;height:22px;background:var(--navy);color:#fff;font-size:11px;font-weight:600;padding:4px 28px}
  .services-note{position:absolute;right:24px;top:210px;font-size:10px;font-style:italic;font-weight:500;color:var(--grey-mid)}
  .services{position:absolute;left:14px;top:232px;width:522px;display:flex;list-style:none}
  .service{flex:1;text-align:center;font-size:7.5px;font-weight:500;color:var(--grey);line-height:1.15}
  .service svg{display:block;margin:0 auto 4px;width:32px;height:32px}
  .address-strip{position:absolute;left:0;top:296px;width:550px;height:20px;background:var(--grey-light);font-size:9px;font-weight:500;color:var(--grey);padding:4px 0 0 160px}
  .address-strip svg{width:8px;height:10px;vertical-align:-1px;margin-right:4px}
  .contact-bar{position:absolute;left:0;top:316px;width:550px;height:51px;background:var(--navy);color:#fff;display:flex;align-items:center;padding:0 24px;gap:30px}
  .contact-bar__label{font-size:12px;font-weight:700}
  .contact-bar__phone{font-size:16px;font-weight:700;display:flex;align-items:center;gap:6px}
  .contact-bar__web{font-size:11px;font-weight:600;display:flex;align-items:center;gap:5px;margin-left:auto}
  .contact-bar svg{fill:none;stroke:#fff;stroke-width:1.6}
</style>
</head>
<body>

<section class="postcard postcard--back">
  <div class="offer">
    <h2 class="offer__title">
      <span class="offer__lead">GET A <em>FREE</em></span>
      <span class="offer__main">RENTAL ANALYSIS</span>
    </h2>
    <div class="offer__rule"></div>
    <div class="offer__band">GET A FREE</div>
    <div class="offer__box">
      <p>Determine the rental value of your property.</p>
      <p>Find out how to get the most out of your investment.</p>
      <p>See if your home fits our management approach.</p>
    </div>
    <div class="offer__cta">
      <div class="offer__cta-label">GIVE US A CALL NOW</div>
      <div class="offer__phone">806-555-0147</div>
      <div class="offer__web">www.bramblecrestpm.com</div>
    </div>
    <div class="offer__stripe"></div>
  </div>
  <div class="mailing">
    <div class="mailing__line" style="top:200px"></div>
    <div class="mailing__line" style="top:225px"></div>
    <div class="mailing__line" style="top:250px"></div>
  </div>
</section>

<section class="postcard postcard--front">
  <div class="brand">
    <div class="brand__name">BRAMBLECREST</div>
    <div class="brand__tag">PROPERTY MANAGEMENT</div>
  </div>
  <div class="photo" role="img" aria-label="Photo of two property managers reviewing a laptop in a bright modern office"></div>
  <h1 class="headline">
    <span class="headline__small">CHOOSE THE RIGHT</span>
    <span class="headline__big">PROPERTY<br>MANAGEMENT</span>
    <span class="headline__small">SYSTEM</span>
  </h1>
  <div class="services-band"></div>
  <div class="services-band__label">OUR SERVICES</div>
  <p class="services-note">We offer full-service property management solutions</p>

  <ul class="services">
    <li class="service"><svg viewBox="0 0 32 32"><circle cx="16" cy="16" r="15" fill="none" stroke="#1d4a8a" stroke-width="1.5"/><path d="M9 16l7-6 7 6v7h-5v-4h-4v4H9z" fill="#5f6063"/></svg>Property<br>Marketing</li>
    <li class="service"><svg viewBox="0 0 32 32"><circle cx="16" cy="16" r="15" fill="none" stroke="#1d4a8a" stroke-width="1.5"/><circle cx="16" cy="12" r="3" fill="#5f6063"/><circle cx="10" cy="14" r="2.3" fill="#5f6063"/><circle cx="22" cy="14" r="2.3" fill="#5f6063"/><path d="M10 22a6 6 0 0 1 12 0zM6 22a4 4 0 0 1 6-3.5M26 22a4 4 0 0 0-6-3.5" fill="#5f6063"/></svg>Tenant<br>Screening</li>
    <li class="service"><svg viewBox="0 0 32 32"><circle cx="16" cy="16" r="15" fill="none" stroke="#1d4a8a" stroke-width="1.5"/><text x="16" y="22" text-anchor="middle" font-family="Montserrat,sans-serif" font-size="17" font-weight="700" fill="#5f6063">$</text></svg>Rent<br>Collection</li>
    <li class="service"><svg viewBox="0 0 32 32"><circle cx="16" cy="16" r="15" fill="none" stroke="#1d4a8a" stroke-width="1.5"/><path d="M10 10h10l2 3h-6z" fill="#5f6063"/><rect x="14" y="12" width="3" height="12" fill="#5f6063"/></svg>Maintenance</li>
    <li class="service"><svg viewBox="0 0 32 32"><circle cx="16" cy="16" r="15" fill="none" stroke="#1d4a8a" stroke-width="1.5"/><circle cx="14" cy="14" r="5" fill="none" stroke="#5f6063" stroke-width="2"/><path d="M18 18l5 5" stroke="#5f6063" stroke-width="2.5"/></svg>Property<br>Inspections</li>
    <li class="service"><svg viewBox="0 0 32 32"><circle cx="16" cy="16" r="15" fill="none" stroke="#1d4a8a" stroke-width="1.5"/><rect x="9" y="9" width="14" height="14" fill="none" stroke="#5f6063" stroke-width="1.5"/><rect x="11" y="17" width="2.5" height="5" fill="#5f6063"/><rect x="15" y="13" width="2.5" height="9" fill="#5f6063"/><rect x="19" y="15" width="2.5" height="7" fill="#5f6063"/></svg>Financial<br>Reporting</li>
    <li class="service"><svg viewBox="0 0 32 32"><circle cx="16" cy="16" r="15" fill="none" stroke="#1d4a8a" stroke-width="1.5"/><path d="M16 8l7 3v5c0 4-3 7-7 8-4-1-7-4-7-8v-5z" fill="#5f6063"/></svg>Evictions</li>
    <li class="service"><svg viewBox="0 0 32 32"><circle cx="16" cy="16" r="15" fill="none" stroke="#1d4a8a" stroke-width="1.5"/><path d="M16 8v15M11 23h10M9 11h14M9 11l-3 6h6zM23 11l-3 6h6z" fill="none" stroke="#5f6063" stroke-width="1.4"/></svg>Legal<br>Guidance</li>
  </ul>

  <div class="address-strip"><svg viewBox="0 0 8 10"><path d="M4 0a3.5 3.5 0 0 0-3.5 3.5C.5 6 4 10 4 10s3.5-4 3.5-6.5A3.5 3.5 0 0 0 4 0z" fill="#5f6063"/></svg>2387 Hollow Pine Road, Lubbock, TX 79852</div>

  <div class="contact-bar">
    <span class="contact-bar__label">GIVE US A CALL NOW</span>
    <span class="contact-bar__phone"><svg width="14" height="14" viewBox="0 0 14 14"><path d="M3 1h2l1 3-1.5 1a7 7 0 0 0 4.5 4.5L10 8l3 1v2a2 2 0 0 1-2 2A10 10 0 0 1 1 3a2 2 0 0 1 2-2z"/></svg>806-555-0147</span>
    <span class="contact-bar__web"><svg width="12" height="12" viewBox="0 0 12 12"><circle cx="6" cy="6" r="5"/><path d="M1 6h10M6 1c2 2 2 8 0 10M6 1c-2 2-2 8 0 10"/></svg>www.bramblecrestpm.com</span>
  </div>
</section>

</body>
</html>
```